Industrial B2B Company Seeks Complete Redesign

We manufacture solid/liquid filtration equipment for manufacturers of chemicals, pharmaceuticals and mining products. We will be redesigning our website; our current design is outdated, and a more modern look is desired. Navigation can be improved. Call to action on the header, such as "Start Here". Video on home page. Designer should incorporate colors from our logo, at least the blues, the brown/gold is optional. Existing website can be found at www.BrindleSeparators.com. Also, we do not make water filters and references to water or water-like images should be avoided.
Number of Pages Required
1 page
Look and feel
Each slider illustrates characteristics of the customer's brand and the style your logo design should communicate.

```html
<!DOCTYPE html>
<html lang="en">
<head>
<meta charset="utf-8">
<title>Brindle Separators — Industrial Filtration</title>
<link href="https://fonts.googleapis.com/css2?family=Poppins:wght@400;500;600;700&display=swap" rel="stylesheet">
<style>
:root{
  --navy:#0b2a4d;
  --navy-deep:#071d38;
  --blue:#1c6cb0;
  --blue-light:#e9f2fa;
  --gold:#c9a13b;
  --cream:#fdf7e6;
  --ink:#1b1f2a;
  --muted:#5b6472;
  --white:#ffffff;
  --star:#f2b21b;
}
*{box-sizing:border-box;margin:0;padding:0}
html,body{width:1200px;height:4272px;overflow:hidden}
body{font-family:"Poppins",sans-serif;color:var(--ink);background:var(--white);position:relative}
.abs{position:absolute}
.section-title{font-weight:700;font-size:30px;color:var(--navy);text-align:center;position:absolute;left:0;width:1200px;z-index:4}
.section-sub{font-size:16px;color:var(--ink);text-align:center;position:absolute;left:0;width:1200px;z-index:4}

/* header */
.site-header{position:absolute;top:0;left:0;width:1200px;height:86px;background:var(--white);z-index:5}
.brand{position:absolute;left:140px;top:24px;display:flex;align-items:center;gap:10px;font-weight:700;font-size:22px;color:var(--blue)}
.brand-dot{width:26px;height:26px;border-radius:50%;background:var(--blue)}
.main-nav{position:absolute;left:505px;top:30px;display:flex;gap:22px;font-size:15px;font-weight:500;color:var(--ink);white-space:nowrap}
.btn-contact{position:absolute;left:836px;top:22px;width:112px;height:40px;background:var(--navy);color:var(--white);border-radius:8px;font-size:14px;font-weight:500;display:flex;align-items:center;justify-content:center}
.header-search{position:absolute;left:962px;top:30px}
.lang{position:absolute;left:1000px;top:27px;display:flex;align-items:center;gap:6px}
.lang-circle{width:28px;height:28px;border-radius:50%;background:linear-gradient(#c8333d 0 50%,#2c3f7a 50%)}

/* hero */
.hero{position:absolute;top:86px;left:0;width:1200px;height:640px;background:linear-gradient(120deg,#1a1e26 0%,#3a3430 40%,#6b5440 70%,#2c2a2c 100%)}
.hero-shade{position:absolute;inset:0;background:linear-gradient(90deg,rgba(6,14,28,.85) 0%,rgba(6,14,28,.45) 55%,rgba(6,14,28,.15) 100%)}
.hero-kicker{position:absolute;left:140px;top:140px;color:var(--white);font-size:15px;font-weight:500;letter-spacing:.5px}
.hero-title{position:absolute;left:140px;top:168px;color:var(--white);font-size:54px;font-weight:700;line-height:64px;width:640px}
.hero-title .accent{color:var(--gold)}
.hero-text{position:absolute;left:140px;top:300px;color:var(--white);font-size:17px;line-height:26px;width:440px}
.btn-learn{position:absolute;left:140px;top:376px;width:110px;height:38px;border-radius:19px;background:var(--navy);color:var(--white);font-size:13px;font-weight:500;display:flex;align-items:center;justify-content:center;border:1px solid rgba(255,255,255,.4)}
.hero-product{position:absolute;left:920px;top:540px;width:130px;height:220px;border-radius:14px;background:linear-gradient(180deg,#d9dadd,#8b8e94);z-index:3}
.hero-wave{position:absolute;left:0;top:610px;z-index:2}

/* why */
.features{position:absolute;top:950px;left:150px;width:900px;display:flex;justify-content:space-between}
.feature{width:190px;text-align:center;font-size:15px;font-weight:500;line-height:22px;color:var(--ink)}
.feature-icon{width:72px;height:72px;margin:0 auto 14px;border-radius:50%;display:flex;align-items:center;justify-content:center}
.feature-icon.active{background:var(--blue)}

/* video */
.video-back{position:absolute;left:170px;top:1206px;width:880px;height:400px;border-radius:40px;background:var(--blue-light)}
.video-frame{position:absolute;left:140px;top:1226px;width:920px;height:400px;border-radius:40px;background:linear-gradient(160deg,#a9cde8 0%,#2f77b4 45%,#1d3f5e 100%);overflow:hidden}
.play{position:absolute;left:570px;top:1378px;width:48px;height:48px;border-radius:50%;background:var(--white);display:flex;align-items:center;justify-content:center}
.play-label{position:absolute;left:550px;top:1434px;width:90px;text-align:center;color:var(--white);font-size:13px}

/* industries */
.industries{position:absolute;top:1720px;left:0;width:1200px;height:650px;background:var(--cream)}
.cards{position:absolute;top:1912px;left:140px;width:920px;display:flex;justify-content:space-between}
.card{width:296px;height:340px;background:var(--white);border-radius:14px;box-shadow:0 6px 18px rgba(0,0,0,.1);position:relative;overflow:hidden}
.card-media{height:180px}
.card-badge{position:absolute;left:128px;top:158px;width:40px;height:40px;border-radius:8px;background:var(--gold);border:3px solid var(--white)}
.card h3{text-align:center;font-size:18px;font-weight:600;margin-top:28px;color:var(--ink)}
.card p{font-size:13px;line-height:20px;color:var(--muted);padding:6px 26px 0;text-align:center}

/* testimonials */
.review-brand{position:absolute;top:2656px;left:0;width:1200px;text-align:center;font-size:28px;font-weight:600;color:var(--blue)}
.review{position:absolute;left:140px;width:440px;height:128px;background:var(--white);border-radius:10px;box-shadow:0 4px 14px rgba(0,0,0,.1)}
.review.shift{left:130px;width:460px}
.review-photo{position:absolute;left:12px;top:18px;width:72px;height:90px;border-radius:6px;background:linear-gradient(#8fa4bb,#4c5d72)}
.review-name{position:absolute;left:100px;top:14px;font-size:13px;font-weight:600}
.review-role{position:absolute;left:100px;top:32px;font-size:11px;color:var(--muted)}
.review-stars{position:absolute;right:24px;top:14px;color:var(--star);font-size:14px;letter-spacing:1px}
.review-text{position:absolute;left:100px;top:56px;width:300px;font-size:12px;line-height:18px;color:var(--ink)}
.globe{position:absolute;left:640px;top:2716px;width:480px;height:520px;border-radius:50%;background:radial-gradient(circle at 40% 45%,#d7d9dd 0%,#b7bbc2 55%,rgba(255,255,255,0) 72%)}

/* cta */
.cta{position:absolute;top:3300px;left:0;width:1200px;height:480px;background:linear-gradient(180deg,#0b2a4d,#0a3360)}
.cta-title{position:absolute;top:3466px;left:0;width:1200px;text-align:center;color:var(--white);font-size:27px;font-weight:700}
.cta-text{position:absolute;top:3510px;left:350px;width:500px;text-align:center;color:var(--white);font-size:15px;line-height:22px}
.btn-quote{position:absolute;top:3584px;left:515px;width:170px;height:40px;border-radius:20px;background:var(--gold);color:var(--white);font-size:13px;font-weight:500;display:flex;align-items:center;justify-content:center;white-space:nowrap}

/* footer */
.site-footer{position:absolute;top:3780px;left:0;width:1200px;height:436px;background:#f4f8fc}
.footer-brand{position:absolute;left:140px;top:3988px;display:flex;align-items:center;gap:10px;font-weight:700;font-size:26px;color:var(--blue)}
.footer-col-title{position:absolute;top:3904px;font-size:22px;font-weight:600;color:var(--navy)}
.quick-links{position:absolute;left:560px;top:3956px;list-style:none;font-size:15px;font-weight:500;color:var(--ink)}
.quick-links li{height:42px}
.quick-links li::before{content:"›";margin-right:10px;color:var(--navy)}
.contact-item{position:absolute;left:780px;display:flex;gap:14px}
.contact-icon{width:34px;height:34px;border-radius:50%;background:var(--navy);display:flex;align-items:center;justify-content:center;flex-shrink:0}
.contact-item strong{display:block;font-size:15px;font-weight:600}
.contact-item span{font-size:13px;color:var(--muted);line-height:19px}
.bottom-bar{position:absolute;top:4216px;left:0;width:1200px;height:56px;background:var(--navy-deep);color:var(--white)}
.copyright{position:absolute;left:140px;top:18px;font-size:13px}
.social{position:absolute;left:890px;top:14px;display:flex;gap:10px}
.social span{width:28px;height:28px;border-radius:50%;border:1.5px solid var(--white)}
</style>
</head>
<body>

<header class="site-header">
  <div class="brand"><span class="brand-dot"></span>Brindle Separators</div>
  <nav class="main-nav"><span>Home</span><span>Products</span><span>Services</span><span>About Us</span></nav>
  <div class="btn-contact">Contact</div>
  <svg class="header-search" width="24" height="24" viewBox="0 0 24 24" fill="none" stroke="#1b1f2a" stroke-width="2.4"><circle cx="10" cy="10" r="7"/><path d="M15 15l6 6"/></svg>
  <div class="lang"><span class="lang-circle"></span><svg width="12" height="8" viewBox="0 0 12 8"><path d="M1 1l5 5 5-5" stroke="#1b1f2a" stroke-width="2" fill="none"/></svg></div>
</header>

<section class="hero" role="img" aria-label="Industrial plant interior with pumps, pipes and filtration machinery">
  <div class="hero-shade"></div>
  <p class="hero-kicker">WELCOME TO BRINDLE SEPARATORS</p>
  <h1 class="hero-title">Optimizing <span class="accent">Industrial</span> Filtration Processes</h1>
  <p class="hero-text">Briefly expand on your headline and highlight your key offerings.</p>
  <div class="btn-learn">Learn More</div>
</section>
<div class="hero-product" role="img" aria-label="Stainless steel filter vessel on a wheeled stand"></div>
<svg class="hero-wave" width="1200" height="160" viewBox="0 0 1200 160">
  <path d="M0 50 C250 10 420 110 640 80 C820 55 960 10 1200 40 L1200 160 L0 160Z" fill="#ffffff"/>
  <path d="M0 50 C250 10 420 110 640 80 C820 55 960 10 1200 40" fill="none" stroke="#1c6cb0" stroke-width="14"/>
  <circle cx="640" cy="80" r="24" fill="#ffffff" stroke="#1c6cb0" stroke-width="10"/>
</svg>

<h2 class="section-title" style="top:790px">Why Choose us</h2>
<p class="section-sub" style="top:838px">Why Choose Brindle Separators?" or "The Brindle Advantage</p>
<div class="features">
  <div class="feature">
    <div class="feature-icon"><svg width="44" height="44" viewBox="0 0 44 44" fill="none" stroke="#0b2a4d" stroke-width="2"><circle cx="22" cy="16" r="10"/><path d="M16 24l-4 14 10-5 10 5-4-14"/></svg></div>
    Proven track record in Industrial filtration
  </div>
  <div class="feature">
    <div class="feature-icon active"><svg width="44" height="44" viewBox="0 0 44 44" fill="none" stroke="#ffffff" stroke-width="2"><circle cx="22" cy="22" r="7"/><path d="M22 6v6M22 32v6M6 22h6M32 22h6M11 11l4 4M29 29l4 4M11 33l4-4M29 15l4-4"/></svg></div>
    High-performance, reliable equipment
  </div>
  <div class="feature">
    <div class="feature-icon"><svg width="44" height="44" viewBox="0 0 44 44" fill="none" stroke="#0b2a4d" stroke-width="2"><circle cx="22" cy="22" r="6"/><circle cx="22" cy="22" r="14" stroke-dasharray="6 4"/></svg></div>
    Customized solutions for specific needs
  </div>
  <div class="feature">
    <div class="feature-icon"><svg width="44" height="44" viewBox="0 0 44 44" fill="none" stroke="#0b2a4d" stroke-width="2"><circle cx="22" cy="15" r="7"/><path d="M9 38c0-8 6-13 13-13s13 5 13 13"/><path d="M12 16c0-6 4-10 10-10s10 4 10 10"/></svg></div>
    Dedicated customer support
  </div>
</div>

<h2 class="section-title" style="top:1122px">Our Video</h2>
<div class="video-back"></div>
<div class="video-frame" role="img" aria-label="Outdoor view of a blue industrial processing plant with tanks and piping"></div>
<div class="play"><svg width="18" height="18" viewBox="0 0 18 18"><path d="M5 3l10 6-10 6z" fill="#0b2a4d"/></svg></div>
<p class="play-label">Watch Video</p>

<section class="industries"></section>
<h2 class="section-title" style="top:1796px">Industry Expertise</h2>
<p class="section-sub" style="top:1842px">Empowering Success Through Industry Expertise</p>
<div class="cards">
  <article class="card">
    <div class="card-media" role="img" aria-label="Chemical laboratory glassware" style="background:linear-gradient(135deg,#e8eef4,#6fa8d6)"></div>
    <span class="card-badge"></span>
    <h3>Chemical</h3>
    <p>Lorem ipsum dolor sit amet, consectetur adipiscing elit, sed do ei dolore magna aliqua.</p>
  </article>
  <article class="card">
    <div class="card-media" role="img" aria-label="Pharmaceutical tablets" style="background:linear-gradient(135deg,#d8e4f2,#3c6fb8)"></div>
    <span class="card-badge"></span>
    <h3>Pharmaceutical</h3>
    <p>Lorem ipsum dolor sit amet, consectetur adipiscing elit, sed do ei dolore magna aliqua.</p>
  </article>
  <article class="card">
    <div class="card-media" role="img" aria-label="Mining processing plant interior" style="background:linear-gradient(135deg,#3b4a5e,#8a7a62)"></div>
    <span class="card-badge"></span>
    <h3>Mining Industries</h3>
    <p>Lorem ipsum dolor sit amet, consectetur adipiscing elit, sed do ei dolore magna aliqua.</p>
  </article>
</div>
<svg class="abs" style="left:0;top:2300px" width="1200" height="180" viewBox="0 0 1200 180">
  <path d="M0 70 L1200 70 L1200 0 L0 0Z" fill="#fdf7e6"/>
  <path d="M0 150 C150 60 300 50 520 70 C760 90 980 60 1200 10 L1200 0 L0 0Z" fill="#fdf7e6"/>
  <path d="M0 150 C150 60 300 50 520 70 C760 90 980 60 1200 10" fill="none" stroke="#c9a13b" stroke-width="16"/>
</svg>

<h2 class="section-title" style="top:2566px">See What Our Client Say About us</h2>
<p class="section-sub" style="top:2614px;font-size:14px">BrindleSeparators Industrial</p>
<p class="review-brand">Reviewly</p>

<div class="review" style="top:2740px">
  <div class="review-photo" role="img" aria-label="Client portrait"></div>
  <p class="review-name">Nolan Ashcroft</p><p class="review-role">Designation</p>
  <p class="review-stars">★★★★★</p>
  <p class="review-text">Lorem Ipsum is simply dummy text of the printing and typesetting industry.</p>
</div>
<div class="review shift" style="top:2898px">
  <div class="review-photo" role="img" aria-label="Client portrait"></div>
  <p class="review-name">Marla Quinby</p><p class="review-role">Designation</p>
  <p class="review-stars">★★★★★</p>
  <p class="review-text">Lorem Ipsum is simply dummy text of the printing and typesetting industry. Lorem Ipsum has been the industry's standard dummy text.</p>
</div>
<div class="review" style="top:3060px">
  <div class="review-photo" role="img" aria-label="Client portrait"></div>
  <p class="review-name">Desmond Varga</p><p class="review-role">Designation</p>
  <p class="review-stars">★★★★★</p>
  <p class="review-text">Lorem Ipsum is simply dummy text of the printing and typesetting industry. Lorem Ipsum has been the industry's standard dummy text.</p>
</div>
<div class="globe" role="img" aria-label="Dotted world globe with client portraits placed around it"></div>

<section class="cta"></section>
<svg class="abs" style="left:0;top:3250px" width="1200" height="120" viewBox="0 0 1200 120">
  <path d="M0 0 L1200 0 L1200 40 C950 100 780 40 600 70 C420 100 250 40 0 80Z" fill="#ffffff"/>
  <path d="M1200 40 C950 100 780 40 600 70 C420 100 250 40 0 80" fill="none" stroke="#1c6cb0" stroke-width="14"/>
  <circle cx="600" cy="70" r="24" fill="#ffffff" stroke="#1c6cb0" stroke-width="10"/>
</svg>
<h2 class="cta-title">Let's Discuss Your Filtration Needs</h2>
<p class="cta-text">Lorem Ipsum is simply dummy text of the printing and typesetting industry. Lorem Ipsum has been the industry's standard dummy</p>
<div class="btn-quote">Requesting a Quote</div>
<svg class="abs" style="left:0;top:3650px" width="1200" height="160" viewBox="0 0 1200 160">
  <path d="M0 60 C200 130 380 110 560 90 C760 70 950 20 1200 80 L1200 160 L0 160Z" fill="#f4f8fc"/>
  <path d="M0 60 C200 130 380 110 560 90 C760 70 950 20 1200 80" fill="none" stroke="#1c6cb0" stroke-width="14"/>
  <circle cx="540" cy="92" r="24" fill="#ffffff" stroke="#1c6cb0" stroke-width="10"/>
</svg>

<footer class="site-footer"></footer>
<div class="footer-brand"><span class="brand-dot" style="width:32px;height:32px"></span>Brindle Separators</div>
<h4 class="footer-col-title" style="left:552px">Quick Links</h4>
<ul class="quick-links"><li>Home</li><li>About Us</li><li>Our Products</li><li>Resources</li><li>Contact</li></ul>
<h4 class="footer-col-title" style="left:780px">Contact Info</h4>
<div class="contact-item" style="top:3958px">
  <span class="contact-icon"><svg width="16" height="16" viewBox="0 0 16 16"><path d="M3 1l3 3-1.5 2a9 9 0 005 5l2-1.5 3 3-2 2C6 14 2 10 1 3z" fill="#fff"/></svg></span>
  <div><strong>Call</strong><span>555-0142</span></div>
</div>
<div class="contact-item" style="top:4024px">
  <span class="contact-icon"><svg width="16" height="16" viewBox="0 0 16 16"><path d="M8 1a5 5 0 015 5c0 4-5 9-5 9S3 10 3 6a5 5 0 015-5z" fill="#fff"/><circle cx="8" cy="6" r="2" fill="#0b2a4d"/></svg></span>
  <div><strong>Address</strong><span>Brindle Separators Inc.<br>48 Ferrow Ridge Road</span></div>
</div>
<div class="contact-item" style="top:4110px">
  <span class="contact-icon"><svg width="16" height="16" viewBox="0 0 16 16"><rect x="1" y="3" width="14" height="10" rx="1" fill="#fff"/><path d="M1 4l7 5 7-5" stroke="#0b2a4d" fill="none"/></svg></span>
  <div><strong>Email</strong><span>hello@brindleseparators.com</span></div>
</div>

<div class="bottom-bar">
  <p class="copyright">© 2024 Brindle Separators Inc. All Rights Reserved.</p>
  <div class="social"><span></span><span></span><span></span><span></span></div>
</div>

</body>
</html>
```